Black Matte card with samurai logo which I would like it to be textured and company name on one side and on the other side I would like the company information with the reno (Face logo) Sushi logo. Double Sided card.

majority customers are University students, University sororities and fraternities.

It Company

Reno Sushi
317 W. Harlow Ave
Tucson, AZ 85042
Phone (520)413-6271
Fax (520)357-1846
E-mail: Renosushidesert@mailbox-example.com
FB: Renosushidesert
Twitter: Renosushidesert

• Present Normal

```html
<!DOCTYPE html>
<html lang="en">
<head>
<meta charset="utf-8">
<title>Reno Sushi – Business Card</title>
<link href="https://fonts.googleapis.com/css2?family=PT+Sans&display=swap" rel="stylesheet">
<style>
  :root {
    --backdrop: #e8e3db;
    --card-black: #1c1c1c;
    --card-white: #ffffff;
    --ink: #4a4a4a;
    --sushi-red: #b3261e;
    --mark-dark: #2b2b2b;
    --divider: #d6d6d6;
  }
  * { margin: 0; padding: 0; box-sizing: border-box; }
  html, body { width: 1200px; height: 1197px; overflow: hidden; }
  body { background: var(--backdrop); position: relative; font-family: "PT Sans", sans-serif; }

  .card { position: absolute; width: 935px; height: 534px; border-radius: 40px; overflow: hidden; }

  /* Front side – textured matte black */
  .card-front { left: 22px; top: 38px; background: var(--card-black); }
  .card-front .texture { position: absolute; inset: 0; width: 935px; height: 534px; }
  .front-brand {
    position: absolute; left: 0; top: 150px; width: 935px;
    display: flex; flex-direction: column; align-items: center;
  }
  .front-brand .brand-dot {
    width: 44px; height: 44px; border-radius: 50%; background: var(--sushi-red); margin-bottom: 26px;
  }
  .front-brand .brand-word {
    color: #ffffff; font-size: 96px; line-height: 1; letter-spacing: 4px; font-weight: 400;
  }
  .card-front .website {
    position: absolute; left: 0; width: 935px; top: 452px;
    text-align: center; color: #ffffff; font-size: 25px; letter-spacing: 2px; line-height: 32px;
  }

  /* Back side */
  .card-back { left: 204px; top: 607px; background: var(--card-white); border: 1.5px solid #222; }
  .card-back .brand-mark {
    position: absolute; left: 162px; top: 60px; width: 120px; height: 120px;
    border-radius: 50%; background: var(--mark-dark);
  }
  .brand-name {
    position: absolute; left: 96px; top: 262px; width: 250px; text-align: center;
    color: var(--sushi-red); font-weight: 400; line-height: 1;
  }
  .brand-name .word-main { display: block; font-size: 78px; }
  .brand-name .word-sub { display: block; font-size: 38px; margin-top: 4px; }
  .divider { position: absolute; left: 414px; top: 78px; width: 1.5px; height: 292px; background: var(--divider); }

  .contact-list { position: absolute; left: 436px; top: 88px; list-style: none; color: var(--ink); font-size: 23.5px; }
  .contact-list li { display: flex; align-items: center; height: 35.7px; white-space: nowrap; }
  .contact-list svg { width: 22px; height: 22px; margin-right: 12px; flex: none; }
  .contact-list .plain-square { width: 20px; height: 20px; margin-right: 14px; border-radius: 3px; flex: none; }
  .plain-square.fb { background: #3b5b99; }
  .plain-square.tw { background: #5fc0e8; }

  .address { position: absolute; left: 436px; top: 294px; color: var(--ink); font-size: 23.5px; line-height: 34px; }

  .waves { position: absolute; left: 0; bottom: 0; width: 935px; height: 534px; }
</style>
</head>
<body>

  <section class="card card-front">
    <svg class="texture" viewBox="0 0 935 534" aria-hidden="true">
      <filter id="matte-grain" x="0" y="0" width="100%" height="100%">
        <feTurbulence type="fractalNoise" baseFrequency="0.28" numOctaves="3" seed="7" result="noise"/>
        <feDiffuseLighting in="noise" lighting-color="#5a5a5a" surfaceScale="2.2" result="lit">
          <feDistantLight azimuth="225" elevation="48"/>
        </feDiffuseLighting>
        <feComponentTransfer in="lit">
          <feFuncR type="linear" slope="0.55" intercept="-0.05"/>
          <feFuncG type="linear" slope="0.55" intercept="-0.05"/>
          <feFuncB type="linear" slope="0.55" intercept="-0.05"/>
        </feComponentTransfer>
      </filter>
      <rect width="935" height="534" filter="url(#matte-grain)"/>
    </svg>
    <div class="front-brand">
      <span class="brand-dot"></span>
      <h2 class="brand-word">Reno Sushi</h2>
    </div>
    <p class="website">www.renosushidesert-example.com</p>
  </section>

  <section class="card card-back">
    <span class="brand-mark"></span>
    <h1 class="brand-name"><span class="word-main">reno</span><span class="word-sub">sushi</span></h1>
    <div class="divider"></div>

    <ul class="contact-list">
      <li>
        <svg viewBox="0 0 24 24" aria-hidden="true"><circle cx="12" cy="12" r="10" fill="none" stroke="#b3261e" stroke-width="1.8"/><path d="M8.5 7.5c.8-.6 1.6-.4 2 .4l.8 1.6c.3.6.1 1.2-.4 1.6l-.6.4c.6 1.4 1.6 2.4 3 3l.4-.6c.4-.5 1-.7 1.6-.4l1.6.8c.8.4 1 1.2.4 2-1.2 1.4-3 1.4-5.4-.4-2.6-2-4.2-5.2-3.4-8.4z" fill="#b3261e"/></svg>
        (520)413-6271
      </li>
      <li>
        <svg viewBox="0 0 24 24" aria-hidden="true"><rect x="6" y="3" width="12" height="19" rx="2" fill="#b3261e"/><rect x="8" y="6" width="8" height="6" fill="#fff"/><rect x="8" y="14" width="8" height="5" fill="#fff" opacity=".6"/></svg>
        (520)357-1846
      </li>
      <li>
        <svg viewBox="0 0 24 24" aria-hidden="true"><rect x="2" y="6" width="20" height="13" rx="1.5" fill="#b3261e"/><path d="M2.5 6.5l9.5 7 9.5-7" fill="none" stroke="#fff" stroke-width="1.6"/></svg>
        Renosushidesert@mailbox-example.com
      </li>
      <li><span class="plain-square fb"></span>Renosushidesert</li>
      <li><span class="plain-square tw"></span>Renosushidesert</li>
    </ul>

    <p class="address">Reno Sushi 317 W. Harlow Ave Tucson<br>AZ 85042</p>

    <svg class="waves" viewBox="0 0 935 534" aria-hidden="true">
      <path d="M0 430 C200 418 430 436 620 472 C740 462 860 428 935 398 L935 428 C860 452 770 470 640 486 C440 468 200 466 0 466 Z" fill="var(--sushi-red)"/>
      <path d="M310 420 C480 430 600 450 690 470 C620 455 480 436 310 420 Z" fill="var(--sushi-red)"/>
      <path d="M0 478 C240 470 480 494 690 492 C800 488 880 466 935 448 L935 534 L0 534 Z" fill="var(--card-black)"/>
    </svg>
  </section>

</body>
</html>
```